Accountability Project Graphics

I want to create 10 social media graphics (new Instagram size 4:5 (1080 x 1350 pixels) focusing on our Quilvo Accountability App, using any of the 3 pictures attached. Use the attached pics only, NO RANDOM STOCK PHOTOGRAPHY. For the color scheme, use the landing page colors/fonts (attached).
You can add any of the 3 photos attached but I mainly need BOLD text that includes these headlines and sub-headlines on them.
Please NOTE for all the headlines below, also add this sub-headline on each graphic:
Stay Consistent with RT in Your Pocket!
Here are the headlines:
• Stop Starting Over Every Monday
• You don't need more willpower. You need more support
• Built for women who are tired of doing this alone
• When Motivation Fades, RT Checks In
• The Support System You've Been Missing
• Support When Motivation Disappears
• What if RT Checked in Every Day?
• The Missing Piece Isn't Another Diet
• Eat the food you love. Stay accountable every day.
• One Bad Meal Doesn't Mean You Failed
women over 40 trying to lose weight

```html
<!DOCTYPE html>
<html lang="en">
<head>
<meta charset="utf-8">
<title>RT Accountability Graphics</title>
<link href="https://fonts.googleapis.com/css2?family=Poppins:wght@600;700;800&family=Yellowtail&family=Pinyon+Script&display=swap" rel="stylesheet">
<style>
:root{
  --page:#fcebee;
  --plum-dark:#45103a;
  --plum:#6a1a4c;
  --blush:#f8bfd3;
  --rose:#d9527f;
  --ink:#2b1240;
  --black:#111;
  --pink-light:#fde8ef;
  --pink-mid:#f9c9da;
  --photo-warm:#b79a86;
  --photo-denim:#3f5275;
  --photo-dark:#2a2230;
}
*{margin:0;padding:0;box-sizing:border-box}
html,body{width:1200px;height:1017px;overflow:hidden;background:var(--page)}
body{position:relative;font-family:"Poppins",sans-serif}
.card{position:absolute;width:306px;height:383px;overflow:hidden}
.card--plum{background:linear-gradient(90deg,var(--plum-dark),var(--plum) 60%)}
.card--pink{background:linear-gradient(135deg,#fff 0%,var(--pink-light) 45%,var(--pink-mid) 100%)}
.abs{position:absolute}
.script{font-family:"Yellowtail","Brush Script MT",cursive;font-weight:400;white-space:nowrap;line-height:1}
.elegant{font-family:"Pinyon Script","Snell Roundhand",cursive;font-weight:400;white-space:nowrap;line-height:1}
.headline{font-weight:700;text-transform:uppercase;line-height:1.1;white-space:nowrap}
.tagline{font-weight:700;font-size:12px;line-height:17px;text-transform:uppercase;text-align:center;white-space:nowrap}
.photo{position:absolute;border-radius:50%}
.ring{position:absolute;border-radius:50%;border:3px solid var(--plum)}

/* card 1 */
.c1{left:86px;top:99px}
.c1 .script{left:0;width:306px;top:20px;text-align:center;font-size:44px;color:var(--pink-light)}
.c1 .headline{left:0;width:306px;top:76px;text-align:center;font-size:24px;line-height:31px;color:var(--blush)}
.c1 .photo{left:66px;top:149px;width:164px;height:164px;background:linear-gradient(100deg,var(--photo-warm),var(--photo-denim) 55%,var(--photo-dark))}
.c1 .ring{left:60px;top:143px;width:176px;height:176px;border-color:#8a2a66}
.c1 .tagline{left:0;width:306px;top:328px;color:#fff}

/* card 2 */
.c2{left:432px;top:99px}
.c2 .script{left:0;width:306px;top:16px;text-align:center;font-size:46px;color:var(--ink)}
.c2 .headline{left:0;width:306px;top:70px;text-align:center;font-size:24px;color:var(--rose)}
.c2 .photo{left:70px;top:128px;width:158px;height:158px;background:linear-gradient(180deg,#e8c8d4,var(--photo-dark) 35%,#1c1820)}
.c2 .ring{left:64px;top:123px;width:170px;height:170px}
.c2 .tagline{left:0;width:306px;top:315px;color:var(--black)}

/* card 3 */
.c3{left:778px;top:99px}
.c3 .photo{left:62px;top:0;width:186px;height:211px;border-radius:0 0 93px 93px;background:linear-gradient(160deg,#8d7a6a,#3a3038 45%,#1c1820 70%,#9c2030)}
.c3 .headline{left:0;width:306px;top:238px;text-align:center;font-size:23px;color:var(--blush)}
.c3 .elegant{left:0;width:306px;top:268px;text-align:center;font-size:36px;color:#fff}
.c3 .tagline{left:0;width:306px;top:323px;color:#fff}

/* card 4 */
.c4{left:280px;top:518px}
.c4 .sweep{position:absolute;left:0;top:0}
.c4 .photo{left:20px;top:140px;width:200px;height:230px;border-radius:40%;background:radial-gradient(circle at 50% 45%,rgba(214,120,160,.35),rgba(240,180,200,0) 70%)}
.c4 .stack{right:17px;top:18px;text-align:right;font-weight:800;text-transform:uppercase;color:var(--ink);font-size:37px;line-height:52px;white-space:nowrap}
.c4 .stack span{display:block}
.c4 .stack .dark{color:var(--black)}
.c4 .stack .accent{color:var(--rose);font-size:31px}
.c4 .tagline{right:120px;top:302px;text-align:right;color:var(--black)}
.c4 .tagline span{display:block}

/* card 5 */
.c5{left:625px;top:518px}
.c5 .headline{left:14px;top:32px;font-size:22px;line-height:31px;color:var(--blush)}
.c5 .tagline{left:15px;top:169px;text-align:left;color:#fff}
.c5 .photo{left:90px;top:211px;width:272px;height:272px;background:linear-gradient(100deg,#cfc6c0,var(--photo-denim) 45%,#e7dfd8 60%,var(--photo-denim) 80%)}
.c5 .outline{position:absolute;left:84px;top:205px;width:290px;height:290px;border-radius:50%;border:1.5px solid var(--pink-light)}
</style>
</head>
<body>

<section class="card card--plum c1">
  <p class="abs script">Built for women</p>
  <h2 class="abs headline">Who are tired of<br>doing this alone</h2>
  <div class="ring"></div>
  <div class="photo" role="img" aria-label="Photo of RT laughing with a client"></div>
  <p class="abs tagline">Stay consistent with RT<br>in your pocket!</p>
</section>

<section class="card card--pink c2">
  <p class="abs script">Stop Starting</p>
  <h2 class="abs headline">Over every Monday</h2>
  <div class="ring"></div>
  <div class="photo" role="img" aria-label="Photo of RT standing with hand on hip"></div>
  <p class="abs tagline">Stay consistent with RT<br>in your pocket!</p>
</section>

<section class="card card--plum c3">
  <div class="photo" role="img" aria-label="Photo of RT leaning on a pool table"></div>
  <h2 class="abs headline">What if RT checked</h2>
  <p class="abs elegant">in Every Day?</p>
  <p class="abs tagline">Stay consistent with RT<br>in your pocket!</p>
</section>

<section class="card card--pink c4">
  <svg class="sweep" width="306" height="383" viewBox="0 0 306 383" aria-hidden="true">
    <path d="M0 0 H40 C200 20 320 150 290 260 C270 330 230 370 200 383 H0 Z" fill="#fff" opacity=".75"/>
    <path d="M0 0 C120 5 250 60 280 130" fill="none" stroke="#d8c4d4" stroke-width="10" opacity=".8"/>
  </svg>
  <div class="photo" role="img" aria-label="Faded photo of RT hugging a client"></div>
  <h2 class="abs stack"><span>When</span><span>Motivation</span><span class="dark">Fades,</span><span class="accent">RT checks in</span></h2>
  <p class="abs tagline"><span>Stay consistent with RT</span><span>in your pocket!</span></p>
</section>

<section class="card card--plum c5">
  <h2 class="abs headline">You don't need<br>more willpower.<br>You need more<br>support</h2>
  <p class="abs tagline">Stay consistent with RT<br>in your pocket!</p>
  <div class="outline"></div>
  <div class="photo" role="img" aria-label="Photo of RT and a client laughing together"></div>
</section>

</body>
</html>
```